Home Fund Guide

Have clients check their mortgage qualifications before they go looking for a mortgage lender. This program gains access to your lenders credit report / 3 scores without impacting your credit scores.

```html
<!DOCTYPE html>
<html lang="en">
<head>
<meta charset="utf-8">
<title>Home Fund Guide – Business Card</title>
<link rel="stylesheet" href="https://fonts.googleapis.com/css2?family=Montserrat:wght@600;700&family=Arimo:wght@400&display=swap">
<style>
  :root {
    --bg: #d9d9da;
    --card: #2e2e31;
    --edge: #1fcf7c;
    --brand-green: #1fcf7c;
    --brand-blue: #1f5fd6;
    --text: #f2f2f2;
    --rule: #8d8d90;
    --emboss: #1f1f21;
  }
  * { box-sizing: border-box; margin: 0; padding: 0; }
  html, body { width: 1200px; height: 801px; overflow: hidden; }
  body {
    background: var(--bg);
    display: flex;
    align-items: center;
    justify-content: center;
    gap: 60px;
    font-family: "Arimo", Arial, sans-serif;
  }
  .card {
    position: relative;
    width: 520px;
    height: 297px;
    background: var(--card);
    border-radius: 26px;
    border-bottom: 5px solid var(--edge);
    overflow: hidden;
  }
  .card__rule {
    position: absolute;
    left: 58px;
    right: 60px;
    top: 166px;
    height: 1px;
    background: var(--rule);
  }
  .brand {
    position: absolute;
    display: flex;
    align-items: center;
    gap: 12px;
    white-space: nowrap;
  }
  .card--front .brand {
    top: 56px;
    right: 60px;
  }
  .brand__mark {
    width: 26px;
    height: 26px;
    background: var(--brand-blue);
    border-radius: 4px;
    flex: none;
  }
  .brand__name {
    font-family: "Montserrat", Arial, sans-serif;
    font-weight: 700;
    font-size: 30px;
    line-height: 1.2;
    color: var(--brand-green);
    letter-spacing: 0.2px;
  }
  .person {
    position: absolute;
    left: 58px;
    top: 114px;
    white-space: nowrap;
  }
  .person__name {
    font-family: "Montserrat", Arial, sans-serif;
    font-weight: 700;
    font-size: 22px;
    color: var(--brand-green);
    line-height: 1.1;
  }
  .person__role {
    font-size: 15px;
    color: var(--text);
    margin-top: 3px;
  }
  .contacts {
    position: absolute;
    left: 74px;
    top: 184px;
    list-style: none;
  }
  .contacts li {
    display: flex;
    align-items: center;
    gap: 10px;
    font-size: 15px;
    color: var(--text);
    line-height: 25px;
    white-space: nowrap;
  }
  .contacts svg { width: 14px; height: 14px; flex: none; }
  .address {
    position: absolute;
    right: 60px;
    top: 196px;
    text-align: right;
    font-size: 14px;
    color: var(--text);
    line-height: 20px;
    white-space: nowrap;
  }
  .card--back .brand {
    top: 50%;
    left: 50%;
    transform: translate(-50%, -50%);
  }
  .card--back .brand__name {
    font-size: 38px;
    color: var(--emboss);
  }
</style>
</head>
<body>
  <section class="card card--front" aria-label="Card front">
    <div class="brand">
      <span class="brand__mark"></span>
      <span class="brand__name">Home Fund Guide</span>
    </div>
    <div class="person">
      <p class="person__name">Daniel Reeves</p>
      <p class="person__role">Manager</p>
    </div>
    <div class="card__rule"></div>
    <ul class="contacts">
      <li>
        <svg viewBox="0 0 14 14" aria-hidden="true"><path d="M3 1.5l2 2.5-1.2 1.4a7 7 0 0 0 4.8 4.8L10 9l2.5 2-1.2 1.6C6 12.5 1.5 8 1.4 2.7z" fill="var(--brand-green)"/></svg>
        555-014-2100
      </li>
      <li>
        <svg viewBox="0 0 14 14" aria-hidden="true"><rect x="1" y="3" width="12" height="8.5" fill="var(--brand-green)"/><path d="M1 3l6 4.8L13 3" stroke="var(--card)" stroke-width="1.2" fill="none"/></svg>
        contact@homefundguide.com
      </li>
      <li>
        <svg viewBox="0 0 14 14" aria-hidden="true"><circle cx="7" cy="7" r="5.8" fill="none" stroke="var(--brand-green)" stroke-width="1.6"/><path d="M1.5 7h11M7 1.3c-2.5 3-2.5 8.4 0 11.4M7 1.3c2.5 3 2.5 8.4 0 11.4" stroke="var(--brand-green)" stroke-width="1.1" fill="none"/></svg>
        www.homefundguide.com
      </li>
    </ul>
    <p class="address">Your address<br>city, state, ZIP 0000</p>
  </section>

  <section class="card card--back" aria-label="Card back">
    <div class="brand">
      <span class="brand__name">Home Fund Guide</span>
    </div>
  </section>
</body>
</html>
```